Aerial Imaging and photgraphy business card

Design a business card with eye catching aerial photo of country side / landscape with a drone in the foreground.
Also contact details.

Target Market(s)

Aerial Imaging photography

Industry/Entity Type

Advertising

Contact Information for Business Card

Rowland
0412965203
Website http://www.skywardvistaphoto.com.au/
email address : skywardvistaphoto.com.au

Colors
e8f1ca
cadf82
9bcb3c
33a6d7
85cae6
cee9f5

Requirements
Must have
• High res photo
• Korvane drone in the foreground Either T4200 and korvane Glidewing or both
Nice to have
• high resolution landscape country photo on the front of the card with a Korvane T4200 drone in the foreground.

```html
<!DOCTYPE html>
<html lang="en">
<head>
<meta charset="utf-8">
<title>Skyward Vista Imaging – Business Card</title>
<link href="https://fonts.googleapis.com/css2?family=Roboto:wght@400;700&display=swap" rel="stylesheet">
<style>
  :root {
    --page-bg: #e4e4e4;
    --card-white: #ffffff;
    --sky-top: #9cc6ea;
    --sky-mid: #cfe3f2;
    --haze: #e6ecef;
    --field-green: #6f9a4a;
    --bush-dark: #3f5a2c;
    --teal-band: #1d7f9a;
    --ink-dark: #333333;
    --ink-mid: #555555;
    --web-green: #2a9a3c;
    --icon-blue: #2f8fd0;
  }
  * { box-sizing: border-box; margin: 0; padding: 0; }
  html, body { width: 1200px; height: 1200px; overflow: hidden; }
  body {
    background: var(--page-bg);
    font-family: "Roboto", Arial, sans-serif;
    display: flex;
    flex-direction: column;
    align-items: center;
    justify-content: center;
    gap: 60px;
  }
  .card {
    position: relative;
    width: 840px;
    height: 490px;
    border-radius: 16px;
    overflow: hidden;
    background: var(--card-white);
    box-shadow: 0 4px 14px rgba(0,0,0,0.18);
  }
  .card-front .landscape-photo {
    position: absolute; inset: 0;
    background:
      radial-gradient(ellipse 60% 45% at 30% 85%, var(--bush-dark), transparent 70%),
      linear-gradient(160deg, var(--sky-top) 0%, var(--sky-mid) 28%, var(--haze) 45%, #b9c9a4 60%, var(--field-green) 78%, #557a3a 100%);
  }
  .card-back .photo-art { position: absolute; inset: 0; }
  .brand {
    position: absolute;
    top: 44px; right: 46px;
    display: flex; align-items: center; gap: 12px;
  }
  .brand-dot {
    width: 22px; height: 22px; border-radius: 50%;
    background: var(--teal-band);
  }
  .brand-name {
    font-weight: 700;
    font-size: 26px;
    color: var(--ink-dark);
    letter-spacing: 0.5px;
  }
  .contact {
    position: absolute;
    right: 46px; top: 200px;
    text-align: right;
  }
  .person-name { font-size: 34px; font-weight: 700; color: var(--ink-dark); }
  .person-role { font-size: 15px; color: var(--ink-mid); margin-top: 2px; margin-bottom: 22px; }
  .contact-line {
    display: flex; justify-content: flex-end; align-items: center; gap: 10px;
    font-size: 19px; color: var(--ink-dark); margin-top: 8px;
  }
  .contact-line svg { width: 18px; height: 18px; flex: none; }
  .web-name { color: var(--web-green); font-weight: 700; }
</style>
</head>
<body>

  <section class="card card-front">
    <div class="landscape-photo" role="img" aria-label="Aerial photo of green countryside and a hazy lake with a camera drone flying in the foreground"></div>
  </section>

  <section class="card card-back">
    <svg class="photo-art" viewBox="0 0 840 490" preserveAspectRatio="none">
      <defs>
        <linearGradient id="skyLand" x1="0" y1="0" x2="0" y2="1">
          <stop offset="0" stop-color="#9cc6ea"/>
          <stop offset="0.45" stop-color="#d7e6f0"/>
          <stop offset="0.7" stop-color="#8ea58a"/>
          <stop offset="1" stop-color="#5d7e45"/>
        </linearGradient>
      </defs>
      <path d="M0 0 H330 C370 90 420 170 440 270 C455 350 450 420 430 490 H0 Z" fill="#1d7f9a"/>
      <path d="M0 0 H312 C352 90 400 170 418 270 C432 350 428 420 408 490 H0 Z" fill="url(#skyLand)" role="img" aria-label="Aerial landscape photo with a camera drone in the foreground"/>
    </svg>

    <div class="brand">
      <span class="brand-dot"></span>
      <span class="brand-name">Skyward Vista Imaging</span>
    </div>

    <div class="contact">
      <div class="person-name">Ellis Grant</div>
      <div class="person-role">Managing Director</div>
      <div class="contact-line">0412965203
        <svg viewBox="0 0 24 24"><path fill="var(--icon-blue)" d="M6.6 10.8a15 15 0 0 0 6.6 6.6l2.2-2.2c.3-.3.7-.4 1-.2 1.1.4 2.3.6 3.6.6.6 0 1 .4 1 1V20c0 .6-.4 1-1 1A17 17 0 0 1 3 4c0-.6.4-1 1-1h3.5c.6 0 1 .4 1 1 0 1.3.2 2.5.6 3.6.1.3 0 .7-.2 1z"/></svg>
      </div>
      <div class="contact-line">hello@skywardvistaphoto.com.au
        <svg viewBox="0 0 24 24"><rect x="2" y="5" width="20" height="14" rx="2" fill="var(--icon-blue)"/><path d="M3 6l9 7 9-7" stroke="#fff" stroke-width="1.6" fill="none"/></svg>
      </div>
      <div class="contact-line">www.<span class="web-name">skywardvistaphoto</span>.com.au
        <svg viewBox="0 0 24 24"><circle cx="12" cy="12" r="10" fill="var(--icon-blue)"/><path d="M2 12h20M12 2c3 3 3 17 0 20M12 2c-3 3-3 17 0 20" stroke="#fff" stroke-width="1.4" fill="none"/></svg>
      </div>
    </div>
  </section>

</body>
</html>
```